High-end law practice specializing in closely held business succession planning and complex estates

Solo practitioner whose practice specializes in high-net worth, complex estate planning needs muliple versions of letterhead black and white, please. Letterhead should incorporate slogan, "Guarding Your Family Legacy is my Life's Work," for one and "Complex Estate Planning"; third with no slogan. All for The Law Office of Marcy Lynn Pettibone, PC, 418 Cedar Hollow Ln., Port Haverly, Maryland 23648, Tel. 757-555-0142 Fax tbd email: marcy@mlplawgroup.example; Marcy Lynn Pettibone, Esq., principal, LICENSED IN MD, PA, DE
Updates

Project Deadline Extended
Reason: My internet service went down and I can only view designs on my smart phone -- it's just too hard to review. So sorry! Working with my ISP now. Please be patient!

Target Market(s)

High net worth clients with complex estate planning needs, family businesses, family farmers, family foresters -- people with unique estate/succession planning needs who need a specialist who understands them.

Industry/Entity Type

Business

Font styles to use
Script

Requirements
Must have
• A high-end look and feel, connoting trustworthiness, special knowledge, and expertise.

```html
<!DOCTYPE html>
<html lang="en">
<head>
<meta charset="utf-8">
<title>Letterhead – The Law Office of Marcy Lynn Pettibone, PC</title>
<link rel="stylesheet" href="https://fonts.googleapis.com/css2?family=Noto+Serif:ital,wght@0,700;1,400&family=Source+Sans+3:ital,wght@0,400;0,700;1,400&family=Arimo&family=Caveat&display=swap">
<style>
  :root {
    --backdrop: #ece9e4;
    --paper: #ffffff;
    --ink: #111111;
    --ink-soft: #6b6b6b;
    --rule: #555555;
    --signature: #1d2a8a;
    --band: #000000;
    --band-text: #ffffff;
  }
  * { margin: 0; padding: 0; box-sizing: border-box; }
  html, body {
    width: 1112px; height: 1200px; overflow: hidden;
    background: var(--backdrop);
  }
  .sheet {
    position: absolute; left: 202px; top: 86px;
    width: 708px; height: 1002px;
    background: var(--paper);
    color: var(--ink);
  }
  .firm-name {
    position: absolute; left: 32px; top: 40px;
    font-family: "Noto Serif", Georgia, serif;
    font-weight: 700; font-size: 21px; line-height: 26px;
    letter-spacing: 0.2px;
  }
  .firm-name .line-two { display: block; margin-top: 1px; }
  .header-rule {
    position: absolute; left: 32px; top: 65px;
    width: 646px; height: 1px; background: var(--rule);
  }
  .practice-area {
    position: absolute; left: 32px; top: 90px;
    font-family: "Noto Serif", Georgia, serif;
    font-style: italic; font-size: 18px;
  }
  .address {
    position: absolute; right: 30px; top: 44px;
    font-family: "Source Sans 3", Arial, sans-serif;
    font-size: 14.5px;
  }
  .contact {
    position: absolute; right: 30px; top: 68px;
    text-align: right;
    font-family: "Source Sans 3", Arial, sans-serif;
    font-size: 14px; line-height: 17.5px;
  }
  .letter {
    position: absolute; left: 34px; top: 273px; width: 640px;
    color: var(--ink-soft);
    font-family: "Arimo", Arial, sans-serif;
    font-size: 15px; line-height: 17.3px;
  }
  .salutation {
    font-family: "Source Sans 3", Arial, sans-serif;
    font-weight: 700; font-size: 16px; margin-bottom: 20px;
  }
  .letter p.body { text-align: justify; margin-bottom: 17px; }
  .closing { margin-top: 56px; }
  .signature {
    font-family: "Caveat", cursive;
    color: var(--signature); font-size: 40px; line-height: 42px;
    margin: 0 0 6px;
  }
  .signer { line-height: 18px; }
  .slogan {
    position: absolute; left: 0; width: 100%; top: 945px;
    text-align: center;
    font-family: "Source Sans 3", Arial, sans-serif;
    font-style: italic; font-size: 14px;
  }
  .credentials-band {
    position: absolute; left: 0; top: 965px;
    width: 100%; height: 27px; background: var(--band);
    color: var(--band-text); text-align: center;
    font-family: "Source Sans 3", Arial, sans-serif;
    font-size: 13.5px; line-height: 27px; letter-spacing: 0.2px;
  }
</style>
</head>
<body>
  <main class="sheet">
    <header>
      <h1 class="firm-name">THE LAW OFFICE<span class="line-two">OF MARCY LYNN PETTIBONE, PC</span></h1>
      <div class="header-rule"></div>
      <div class="practice-area">Complex Estate Planning</div>
      <div class="address">Pc, 418 Cedar Hollow Ln., Port Haverly, Maryland 23648</div>
      <div class="contact">
        757-555-0142<br>
        757-555-0199<br>
        marcy@mlplawgroup.example
      </div>
    </header>

    <section class="letter">
      <p class="salutation">Dear Mr. John,</p>
      <p class="body">Lorem Ipsum is simply dummy text of the printing and typesetting industry. Lorem Ipsum has been the industry's standard dummy text ever since the 1500s, when an unknown printer took a galley of type and scrambled it to make a type specimen book. It has survived not only five centuries, but also the leap into electronic typesetting, remaining essentially unchanged.</p>
      <p class="body">The standard chunk of Lorem Ipsum used since the 1500s is reproduced below for those interested. Sections 1.10.32 and 1.10.33 from "de Finibus Bonorum et Malorum" by Calvinus are also reproduced in their exact original form, accompanied by English versions from the 1914 translation by H. Pembrook</p>
      <p class="body">Lorem Ipsum is simply dummy text of the printing and typesetting industry. Lorem Ipsum has been the industry's standard dummy text ever since the 1500s, when an unknown printer took a galley of type and scrambled it to make a type specimen book. It has survived not only five centuries, but also the leap into electronic typesetting, remaining essentially unchanged. It was popularised in the</p>
      <p class="closing">Sincerely Your,</p>
      <p class="signature">your name</p>
      <p class="signer">Name Last Name<br>Company Name</p>
    </section>

    <footer>
      <p class="slogan">Guarding Your Family Legacy is my Life's Work</p>
      <p class="credentials-band">MARCY LYNN PETTIBONE, ESQ., PRINCIPAL, LICENSED IN MD, PA, DE</p>
    </footer>
  </main>
</body>
</html>
```